Internet Of Things brochure

Need to create a brochure with a common theme to our website and the last 2 pages of the attached file. All the contect is in the file that I have attached.
website www.pendomar.com.au

```html
<!DOCTYPE html>
<html lang="en">
<head>
<meta charset="utf-8">
<title>Smart Cities Initiative – IoT Brochure Spread</title>
<link href="https://fonts.googleapis.com/css2?family=Exo+2:wght@400;600;700&display=swap" rel="stylesheet">
<style>
  :root{
    --bg:#9a9a9a;
    --navy:#1d4c86;
    --deep:#173f74;
    --mid:#2f7fb5;
    --cyan:#4fc3e6;
    --sky:#7fd6ef;
    --pale:#bfe9f7;
    --white:#ffffff;
    --sim:#f2c531;
  }
  *{box-sizing:border-box;margin:0;padding:0}
  html,body{width:1200px;height:1200px;overflow:hidden;background:var(--bg);font-family:"Exo 2",sans-serif;color:var(--white)}
  .spread{position:absolute;left:40px;top:320px;width:1120px;height:560px;display:flex;box-shadow:0 10px 30px rgba(0,0,0,.25)}
  .page{position:relative;width:560px;height:560px;overflow:hidden}
  .page--left{background:linear-gradient(170deg,var(--navy) 0%,var(--mid) 55%,var(--cyan) 100%)}
  .page--right{background:linear-gradient(170deg,var(--deep) 0%,var(--mid) 50%,var(--sky) 100%)}
  .spine{position:absolute;left:545px;top:0;width:30px;height:560px;background:linear-gradient(90deg,rgba(255,255,255,0),rgba(255,255,255,.35),rgba(255,255,255,0));z-index:2}

  .intro{position:absolute;left:30px;top:40px;width:180px;font-size:9.5px;line-height:1.45;opacity:.9}
  .title{position:absolute;left:250px;top:40px;font-size:20px;font-weight:700;color:var(--sky)}
  .pillars{position:absolute;left:240px;top:85px;width:300px;list-style:none}
  .pillar{display:flex;gap:14px;margin-bottom:20px}
  .pillar svg{flex:0 0 44px;height:44px}
  .pillar h3{font-size:10px;font-weight:700;text-transform:uppercase;margin-bottom:2px}
  .pillar p{font-size:8.5px;line-height:1.4;opacity:.9}

  .bands{position:absolute;left:0;top:0;width:102px;height:560px;display:flex}
  .band{flex:0 0 34px;width:34px;height:560px;border-right:2px solid var(--sky);display:flex;align-items:center;justify-content:center;overflow:hidden}
  .band span{writing-mode:vertical-rl;transform:rotate(180deg);white-space:nowrap;font-size:9px;letter-spacing:.5px;text-transform:uppercase}
  .band:nth-child(1){background:#1f5a93}
  .band:nth-child(2){background:#23669f}
  .band:nth-child(3){background:#2a73ab}

  .stack{position:absolute;left:114px;top:30px;width:250px}
  .layer{position:relative;height:64px;margin-bottom:12px;padding:6px 8px;font-size:8px;line-height:1.35}
  .layer__name{position:absolute;right:8px;bottom:6px;font-size:10px}
  .layer--apps{background:var(--pale);color:var(--navy)}
  .layer--platform{background:var(--cyan)}
  .layer--cloud{background:#3aa9d6}
  .layer--network{background:#2f88bf}
  .layer--access{background:#2467a1}
  .layer--devices{background:var(--deep)}
  .skyline{position:absolute;left:8px;top:6px;width:170px;height:40px;background:linear-gradient(90deg,#e6f7fd,#a9dff2);border-radius:2px}

  .help{position:absolute;left:378px;top:40px;width:160px;font-size:8.2px;line-height:1.4}
  .help h2{font-size:12px;font-weight:700;color:var(--pale);margin-bottom:6px;line-height:1.2}
  .help ol{padding-left:12px;margin-top:6px}
  .help li{margin-bottom:5px}
  .connect{position:absolute;left:378px;top:400px;width:170px;height:130px}
  .vending{position:absolute;left:470px;top:410px;width:62px;height:110px;border:2px solid var(--white);background:linear-gradient(180deg,#8fd6ee,#5bb8de)}
</style>
</head>
<body>
<main class="spread">
  <section class="page page--left">
    <p class="intro">A smart city is an urban development vision to integrate multiple information and communication technology (ICT) and Internet of Things (IoT) solutions in a secure fashion to manage a city's assets – the city's assets include, but are not limited to, local departments' information systems, schools, libraries, transportation systems, hospitals, power plants, water supply networks, waste management, law enforcement, and other community services. The goal of building a smart city is to improve quality of life by using urban informatics and technology to improve the efficiency of services and meet residents' needs. ICT allows city officials to interact directly with the community and the city infrastructure and to monitor what is happening in the city, how the city is evolving, and how to enable a better quality of life. Through the use of sensors integrated with real-time monitoring systems, data are collected from citizens and devices – then processed and analyzed. The information and knowledge gathered are keys to tackling inefficiency. Pendomar has the ability and partners to push these solutions forward. Pendomar and Corvale together with the Nimbus Cloud partnership have never been easier and cost effective to deploy and capitalize on.</p>
    <h1 class="title">Smart Cities Initiative</h1>
    <ul class="pillars">
      <li class="pillar">
        <svg viewBox="0 0 44 44" fill="none" stroke="#fff" stroke-width="2"><rect x="4" y="10" width="36" height="20" rx="10"/><path d="M12 30l-4 8 10-8"/><circle cx="15" cy="20" r="2.5"/><circle cx="22" cy="20" r="2.5"/><circle cx="29" cy="20" r="2.5"/></svg>
        <div><h3>Smart Governance</h3><p>Interconnected within-city and across-city governance, including ICT-enabled services and interactions between public and private sectors.</p></div>
      </li>
      <li class="pillar">
        <svg viewBox="0 0 44 44" fill="none" stroke="#fff" stroke-width="2"><circle cx="22" cy="16" r="11"/><path d="M22 27v13M22 22l-5-5M22 20l5-4"/></svg>
        <div><h3>Smart Environment</h3><p>Smart energy including renewables, ICT-enabled energy grids, pollution control and monitoring, green buildings and green urban planning.</p></div>
      </li>
      <li class="pillar">
        <svg viewBox="0 0 44 44" fill="none" stroke="#fff" stroke-width="2"><circle cx="22" cy="22" r="16"/><ellipse cx="22" cy="22" rx="7" ry="16"/><path d="M6 22h32M9 14h26M9 30h26"/></svg>
        <div><h3>Smart Economy</h3><p>E-business and commerce, ICT-enabled manufacturing and delivery of services, as well as new products, new services and business models.</p></div>
      </li>
      <li class="pillar">
        <svg viewBox="0 0 44 44" fill="none" stroke="#fff" stroke-width="2"><path d="M22 8a10 10 0 0 0-6 18v6h12v-6a10 10 0 0 0-6-18z"/><path d="M17 36h10M22 2v3M8 8l2 2M36 8l-2 2"/></svg>
        <div><h3>Smart People</h3><p>Those with e-skills, working in ICT-enabled roles, having access to education and training, human resources and capacity management.</p></div>
      </li>
      <li class="pillar">
        <svg viewBox="0 0 44 44" fill="none" stroke="#fff" stroke-width="2"><circle cx="10" cy="28" r="7"/><circle cx="34" cy="28" r="7"/><path d="M10 28l8-12h10l6 12M18 16l4 12h6M16 12h6"/></svg>
        <div><h3>Smart Mobility</h3><p>ICT supported and integrated transport and logistics. Sustainable, safe and interconnected systems for public transport, cars, bicycles and pedestrians.</p></div>
      </li>
      <li class="pillar">
        <svg viewBox="0 0 44 44" fill="none" stroke="#fff" stroke-width="2.5"><circle cx="10" cy="34" r="3" fill="#fff"/><path d="M8 22a14 14 0 0 1 14 14M8 12a24 24 0 0 1 24 24"/></svg>
        <div><h3>Smart Living</h3><p>ICT-enabled lifestyles, behaviour and consumption. Healthy and safe living in a culturally vibrant city with good quality housing.</p></div>
      </li>
    </ul>
  </section>

  <div class="spine"></div>

  <section class="page page--right">
    <div class="bands">
      <div class="band"><span>Services</span></div>
      <div class="band"><span>IoT &amp; Cyber Security</span></div>
      <div class="band"><span>Context-aware service management</span></div>
    </div>

    <div class="stack">
      <div class="layer layer--apps"><div class="skyline" role="img" aria-label="Line drawing of a city skyline with vehicles"></div><span class="layer__name">City applications</span></div>
      <div class="layer layer--platform">CORE platform<br>· Device management<br>· Connectivity management<br>· Data collection &amp; analytics<span class="layer__name">City IoT platform</span></div>
      <div class="layer layer--cloud">Software<br>Defined<br>Network &nbsp;&nbsp;&nbsp; DC Interconnect &nbsp; IP Comms<span class="layer__name">City cloud</span></div>
      <div class="layer layer--network">IP/MPLS<br>Edge &amp; Core &nbsp;&nbsp;&nbsp;&nbsp;&nbsp;&nbsp; IoT Optimized Core<span class="layer__name">City shared network</span></div>
      <div class="layer layer--access">Mobile &amp; Fixed Access<br>IP Backhaul<br>Small Cells/WLAN/LPWAN<span class="layer__name">City-wide access</span></div>
      <div class="layer layer--devices"><span class="layer__name">City devices &amp; sensors</span></div>
    </div>

    <div class="help">
      <h2>How we help you get the most from your IoT and M2M solutions</h2>
      <p>We are committed to delivering connected solutions that transform business productivity. We believe that IoT technology is changing the way businesses operate, helping to drive operational efficiency, customer experience and unlocking new revenue streams. Our commitment is demonstrated through:</p>
      <ol>
        <li>Australia's largest mobile network, including narrowband IoT, providing greater coverage and a range of connectivity options to you.</li>
        <li>Ongoing investment in services, platforms and partners to enable innovative IoT solutions.</li>
        <li>Continued focus on helping businesses across all industries understand and adopt IoT technology.</li>
        <li>Our uncompromising dedication to customer service.</li>
        <li>Our ability to deliver innovative end-to-end IoT solutions.</li>
      </ol>
    </div>

    <svg class="connect" viewBox="0 0 170 130" fill="none" stroke="#fff" stroke-width="2">
      <circle cx="20" cy="28" r="18"/>
      <path d="M10 26a14 14 0 0 1 20 0M14 31a8 8 0 0 1 12 0"/><circle cx="20" cy="36" r="2" fill="#fff"/>
      <path d="M40 28h50" stroke-dasharray="4 3"/>
      <rect x="8" y="70" width="28" height="38" fill="#fff" stroke="none"/>
      <rect x="10" y="88" width="24" height="18" fill="var(--sim)" stroke="none"/>
      <path d="M22 108v12h70" stroke-dasharray="4 3"/>
    </svg>
    <div class="vending" role="img" aria-label="Line drawing of a connected vending machine"></div>
  </section>
</main>
</body>
</html>
```